Stationary Set Rebrand for Brennick

We are a Canadian Distribution and Service Company that was established in 1969. Over the past 5 decades we have expanded our business and have warehouses across Canada. We specialize in adhesive tapes, adhesives, films, safety, warehouse, shipping, janitorial and packaging supplies.

We have updated our logo design and would like a new corporate branding identity that includes a new fresh Stationary Set (Business Cards, Letterhead, Letterhead MS Word, Envelope, Presentation Folders, Email Signatures, Notepad Covers, etc.)

Target Market(s)

Industrial Business Sector

Font styles to use
Sans Serif

Colors
0054AA
0677BA
7BADD7
CADEEF
E8F1F8
0094D4
00A9DD
6FCCEA
C7EBF8
E9F6FB
00AB8E
00BBA5
67D7C9
C6EFE9
E9F9F6
EB3D1F
EC4F4E
F09395
F8D3D4
FCEDEE

Requirements
Should not have
• Colors not too light, darker colours preferred

```html
<!DOCTYPE html>
<html lang="en">
<head>
<meta charset="utf-8">
<title>Brennick Stationery Set</title>
<link href="https://fonts.googleapis.com/css2?family=Barlow:wght@400;500;800&family=Arimo:wght@400&display=swap" rel="stylesheet">
<style>
  :root {
    --bg: #3b3b3d;
    --ink: #231f20;
    --red: #d71f27;
    --paper: #f6f2f3;
    --white: #ffffff;
    --muted: #555052;
    --rule: #c9c4c6;
  }
  * { box-sizing: border-box; margin: 0; padding: 0; }
  html, body { width: 1200px; height: 933px; overflow: hidden; }
  body { background: var(--bg); font-family: "Barlow", sans-serif; color: var(--ink); position: relative; }
  .piece { position: absolute; box-shadow: 0 3px 10px rgba(0,0,0,.35); }

  .brand { display: inline-flex; align-items: center; gap: .18em; font-family: "Barlow", sans-serif; font-weight: 800; line-height: 1; letter-spacing: -.01em; color: var(--ink); }
  .brand--light { color: var(--white); }
  .brand__mark { width: .28em; height: .28em; background: var(--red); align-self: flex-end; margin-bottom: .12em; }

  .contact { font-size: 5.2px; line-height: 1.3; color: var(--ink); }
  .contact li { list-style: none; display: flex; align-items: center; gap: 3px; }
  .contact svg { width: 4px; height: 4px; fill: var(--red); flex: none; }
  .contact--light { color: var(--white); }

  /* Business card */
  .card-front { left: 38px; top: 102px; width: 219px; height: 125px; background: var(--white); border-radius: 6px; }
  .card-front .brand { position: absolute; left: 12px; top: 16px; font-size: 21px; }
  .card-front .address { position: absolute; left: 12px; top: 65px; font-size: 5.4px; line-height: 1.25; }
  .card-front .contact { position: absolute; left: 12px; top: 86px; }
  .card-front .holder { position: absolute; right: 12px; top: 75px; text-align: right; }
  .holder__name { font-weight: 800; font-size: 8.5px; color: var(--red); letter-spacing: .02em; }
  .holder__role { font-size: 5px; color: var(--muted); }
  .card-front .tab { position: absolute; right: 0; top: 76px; width: 5px; height: 15px; background: var(--red); }
  .card-back { left: 34px; top: 275px; width: 223px; height: 128px; background: var(--ink); border-radius: 5px; display: flex; align-items: center; justify-content: center; }
  .card-back .brand { font-size: 34px; }

  /* Letterhead */
  .letterhead { left: 280px; top: 44px; width: 306px; height: 432px; background: var(--paper); }
  .letterhead .brand { position: absolute; left: 31px; top: 28px; font-size: 19px; }
  .letterhead .head-contact { position: absolute; right: 29px; top: 30px; display: flex; gap: 5px; font-size: 5px; line-height: 1.25; }
  .head-contact .address { text-align: right; padding-right: 5px; border-right: .6px solid var(--ink); }
  .letterhead .contact { font-size: 5px; line-height: 1.25; }
  .letter-body { position: absolute; left: 30px; right: 29px; top: 105px; font-family: "Arimo", sans-serif; color: var(--muted); }
  .letter-body .greeting { font-size: 8.5px; margin-bottom: 14px; }
  .letter-body p.text { font-size: 4.6px; line-height: 1.58; text-align: justify; margin-bottom: 6px; }
  .letter-body .closing { font-size: 4.8px; margin-top: 10px; }
  .signature { width: 42px; height: 16px; margin: 4px 0 5px; background: linear-gradient(90deg, #e6e1e2, #efeaeb); }
  .signer { font-size: 6.8px; }
  .signer-role { font-size: 5px; }
  .band { position: absolute; left: 0; right: 0; bottom: 0; background: var(--red); }
  .letterhead .band { height: 7px; }

  /* Compliments slip */
  .slip { left: 632px; top: 80px; width: 312px; height: 85px; background: var(--paper); }
  .slip .brand { position: absolute; left: 71px; top: 29px; font-size: 21px; }
  .slip .divider { position: absolute; left: 167px; top: 22px; width: .6px; height: 40px; background: var(--ink); }
  .slip .details { position: absolute; left: 177px; top: 22px; font-size: 5px; line-height: 1.25; }
  .slip .contact { font-size: 5px; margin-top: 4px; }
  .slip .band { height: 6px; }

  /* Envelope */
  .envelope-back { left: 632px; top: 198px; width: 343px; height: 157px; background: var(--paper); overflow: hidden; }
  .envelope-back svg { position: absolute; left: 0; top: 0; }
  .envelope-back .brand { position: absolute; left: 0; right: 0; top: 17px; justify-content: center; font-size: 26px; }
  .envelope-front { left: 613px; top: 300px; width: 345px; height: 157px; background: var(--paper); }
  .envelope-front .brand { position: absolute; left: 17px; top: 18px; font-size: 20px; }
  .envelope-front .address { position: absolute; left: 17px; top: 102px; font-size: 5.2px; line-height: 1.25; }
  .envelope-front .contact { position: absolute; left: 17px; top: 118px; font-size: 5.2px; }
  .envelope-front .band { height: 6px; }

  /* Notepads */
  .notepad { width: 128px; height: 188px; }
  .notepad-dark { left: 1024px; top: 77px; background: var(--ink); }
  .notepad-light { left: 1026px; top: 297px; background: var(--paper); }
  .spiral { position: absolute; left: 6px; right: 6px; top: -6px; height: 10px; display: flex; justify-content: space-between; }
  .spiral span { width: 1.4px; height: 10px; background: #cfcfcf; border-radius: 1px; }
  .notepad-light .spiral span { background: #2a2a2a; }
  .notepad-dark .brand { position: absolute; left: 0; right: 0; top: 83px; justify-content: center; font-size: 20px; }
  .notepad .web { position: absolute; left: 0; right: 0; bottom: 12px; text-align: center; font-size: 5px; }
  .notepad-dark .web { color: var(--white); }
  .notepad-light .brand { position: absolute; left: 0; right: 0; top: 20px; justify-content: center; font-size: 13px; }
  .ruled { position: absolute; left: 13px; right: 12px; top: 55px; }
  .ruled span { display: block; height: 10.7px; border-bottom: .6px solid var(--rule); }

  /* Folder cover */
  .folder-cover { left: 47px; top: 560px; width: 510px; height: 321px; background: var(--white); }
  .folder-cover .spine { position: absolute; left: 0; top: 0; width: 254px; height: 100%; background: var(--ink); }
  .folder-cover .spine .brand { position: absolute; left: 0; right: 0; top: 137px; justify-content: center; font-size: 37px; }
  .folder-cover .spine .address { position: absolute; left: 0; right: 0; top: 250px; text-align: center; color: var(--white); font-size: 5.2px; line-height: 1.25; }
  .folder-cover .spine .rule { position: absolute; left: 113px; top: 268px; width: 29px; height: .6px; background: var(--white); }
  .folder-cover .spine .contact { position: absolute; left: 0; right: 0; top: 276px; display: grid; grid-template-columns: auto auto; justify-content: center; column-gap: 6px; font-size: 5.2px; }
  .folder-cover .front-brand { position: absolute; left: 254px; right: 0; top: 133px; justify-content: center; font-size: 44px; }
  .folder-cover .band { left: 254px; height: 7px; }

  /* Folder inside */
  .folder-inside { left: 610px; top: 562px; width: 510px; height: 322px; background: linear-gradient(90deg, #ffffff 0%, #eeeeee 48%, #dcdcdc 50%, #f0f0f0 53%, #ffffff 100%); }
  .folder-inside svg { position: absolute; left: 0; top: 0; }
  .folder-inside .brand { position: absolute; top: 238px; font-size: 34px; }
  .folder-inside .pocket-left { left: 55px; }
  .folder-inside .pocket-right { left: 318px; }
</style>
</head>
<body>

<svg width="0" height="0" style="position:absolute" aria-hidden="true">
  <symbol id="icon-phone" viewBox="0 0 10 10"><path d="M2 .5 3.8 2.6 2.9 3.8c.7 1.5 1.8 2.6 3.3 3.3l1.2-.9L9.5 8 8.4 9.5C4.2 9 1 5.8.5 1.6Z"/></symbol>
  <symbol id="icon-mobile" viewBox="0 0 10 10"><path d="M2.5 0h5v10h-5Zm1 1v7h3V1Z"/></symbol>
  <symbol id="icon-mail" viewBox="0 0 10 10"><path d="M0 2h10v6H0Zm1 1 4 2.5L9 3Z"/></symbol>
  <symbol id="icon-web" viewBox="0 0 10 10"><circle cx="5" cy="5" r="5"/></symbol>
</svg>

<!-- Business card front -->
<section class="piece card-front">
  <div class="brand">Brennick<span class="brand__mark"></span></div>
  <p class="address">412 Cedarview Road<br>Halton, Canada 58120</p>
  <ul class="contact">
    <li><svg><use href="#icon-phone"/></svg>555-201-4870</li>
    <li><svg><use href="#icon-mobile"/></svg>555-309-7612</li>
    <li><svg><use href="#icon-mail"/></svg>info@brennick.com</li>
    <li><svg><use href="#icon-web"/></svg>www.brennick.com</li>
  </ul>
  <div class="holder">
    <p class="holder__name">DANIEL MERCER</p>
    <p class="holder__role">President</p>
  </div>
  <span class="tab"></span>
</section>

<!-- Business card back -->
<section class="piece card-back">
  <div class="brand brand--light">Brennick<span class="brand__mark"></span></div>
</section>

<!-- Letterhead -->
<section class="piece letterhead">
  <div class="brand">Brennick<span class="brand__mark"></span></div>
  <div class="head-contact">
    <p class="address">412 Cedarview Road<br>Halton, Canada 58120<br>info@brennick.com</p>
    <ul class="contact">
      <li><svg><use href="#icon-phone"/></svg>555-201-4870</li>
      <li><svg><use href="#icon-mobile"/></svg>555-309-7612</li>
      <li><svg><use href="#icon-web"/></svg>www.brennick.com</li>
    </ul>
  </div>
  <div class="letter-body">
    <p class="greeting">Dear Mr. Harlow,</p>
    <p class="text">Lorem ipsum dolor sit amet, consectetur adipiscing elit. Donec orci purus, luctus vitae dignissim eu, iaculis sed purus. Vivamus faucibus, ipsum nec aliquet viverra, leo mauris condimentum ligula, sit amet sagittis enim ligula quis arcu. Nam egestas tortor id nisi porttitor mattis. In tortor ante, ultricies in suscipit a, tempus non massa. Vivamus et auctor mi. Fusce vel massa nulla. Phasellus nec eros mauris, et scelerisque orci.</p>
    <p class="text">Donec malesuada orci vitae nulla accumsan porta a id massa. Quisque accumsan iaculis magna sit amet fringilla. Maecenas consequat, magna eget tincidunt semper, odio nibh rutrum mi, id feugiat ante nisi eu risus. Vestibulum nunc orci, rhoncus a placerat in, ultricies in mi. Cras mattis varius eros, vel fringilla nisi suscipit eget. Quisque scelerisque sagittis nulla at porttitor.</p>
    <p class="text">Sed id augue vitae urna euismod commodo aliquet a quam. Pellentesque arcu velit, cursus et malesuada ut, consequat et diam. Nullam erat sem, rhoncus id ullamcorper vitae, rhoncus et arcu. In ultricies ultricies nulla, ut rutrum nisi iaculis at. Donec eu magna a metus ornare faucibus. Fusce aliquet faucibus ultricies. Morbi semper, est id tincidunt gravida, sem arcu adipiscing lacus, ac bibendum nulla leo eu purus. Quisque nec diam sed risus consectetur a cumsan quis quis nibh. Vestibulum id purus lorem.</p>
    <p class="text">It is a long established fact that a reader will be distracted by the readable content of a page when looking at its layout. The point of using Lorem Ipsum is that it has a more-or-less normal distribution of letters, as opposed to using 'Content here, content here', making it look like readable English. Many desktop publishing packages</p>
    <p class="closing">Sincerely,</p>
    <div class="signature" role="img" aria-label="Handwritten signature"></div>
    <p class="signer">Daniel Mercer</p>
    <p class="signer-role">CEO/ Founder</p>
  </div>
  <span class="band"></span>
</section>

<!-- Compliments slip -->
<section class="piece slip">
  <div class="brand">Brennick<span class="brand__mark"></span></div>
  <span class="divider"></span>
  <div class="details">
    <p>412 Cedarview Road<br>Halton, Canada 58120</p>
    <ul class="contact">
      <li><svg><use href="#icon-phone"/></svg>555-201-4870</li>
      <li><svg><use href="#icon-mobile"/></svg>555-309-7612</li>
      <li><svg><use href="#icon-mail"/></svg>info@brennick.com</li>
      <li><svg><use href="#icon-web"/></svg>www.brennick.com</li>
    </ul>
  </div>
  <span class="band"></span>
</section>

<!-- Envelope back -->
<section class="piece envelope-back">
  <svg width="343" height="157" viewBox="0 0 343 157" aria-hidden="true">
    <path d="M0 0H343L333 42Q329 57 313 57H30Q14 57 10 42Z" fill="var(--ink)"/>
  </svg>
  <div class="brand brand--light">Brennick<span class="brand__mark"></span></div>
</section>

<!-- Envelope front -->
<section class="piece envelope-front">
  <div class="brand">Brennick<span class="brand__mark"></span></div>
  <p class="address">412 Cedarview Road<br>Halton, Canada 58120</p>
  <ul class="contact">
    <li><svg><use href="#icon-phone"/></svg>555-201-4870</li>
    <li><svg><use href="#icon-mobile"/></svg>555-309-7612</li>
    <li><svg><use href="#icon-mail"/></svg>info@brennick.com</li>
    <li><svg><use href="#icon-web"/></svg>www.brennick.com</li>
  </ul>
  <span class="band"></span>
</section>

<!-- Notepad cover -->
<section class="piece notepad notepad-dark">
  <div class="spiral"><span></span><span></span><span></span><span></span><span></span><span></span><span></span><span></span><span></span><span></span><span></span><span></span><span></span><span></span><span></span><span></span><span></span><span></span><span></span><span></span></div>
  <div class="brand brand--light">Brennick<span class="brand__mark"></span></div>
  <p class="web">www.brennick.com</p>
</section>

<!-- Notepad sheet -->
<section class="piece notepad notepad-light">
  <div class="spiral"><span></span><span></span><span></span><span></span><span></span><span></span><span></span><span></span><span></span><span></span><span></span><span></span><span></span><span></span><span></span><span></span><span></span><span></span><span></span><span></span></div>
  <div class="brand">Brennick<span class="brand__mark"></span></div>
  <div class="ruled"><span></span><span></span><span></span><span></span><span></span><span></span><span></span><span></span><span></span><span></span><span></span></div>
  <p class="web">www.brennick.com</p>
</section>

<!-- Presentation folder cover -->
<section class="piece folder-cover">
  <div class="spine">
    <div class="brand brand--light">Brennick<span class="brand__mark"></span></div>
    <p class="address">412 Cedarview Road<br>Halton, Canada 58120</p>
    <span class="rule"></span>
    <ul class="contact contact--light">
      <li><svg><use href="#icon-phone"/></svg>555-201-4870</li>
      <li><svg><use href="#icon-mobile"/></svg>555-309-7612</li>
      <li><svg><use href="#icon-mail"/></svg>info@brennick.com</li>
      <li><svg><use href="#icon-web"/></svg>www.brennick.com</li>
    </ul>
  </div>
  <div class="brand front-brand">Brennick<span class="brand__mark"></span></div>
  <span class="band"></span>
</section>

<!-- Presentation folder inside -->
<section class="piece folder-inside">
  <svg width="510" height="322" viewBox="0 0 510 322" aria-hidden="true">
    <path d="M0 191H237Q250 191 252 204L255 316L255 322H0Z" fill="var(--ink)"/>
    <path d="M510 191H273Q260 191 258 204L255 316L255 322H510Z" fill="var(--ink)"/>
    <path d="M0 191H233Q238 191 239 198L255 317L271 198Q272 191 277 191H510V322H0Z" fill="var(--ink)"/>
  </svg>
  <div class="brand brand--light pocket-left">Brennick<span class="brand__mark"></span></div>
  <div class="brand brand--light pocket-right">Brennick<span class="brand__mark"></span></div>
</section>

</body>
</html>
```